Social Media Graphics - Oakline Push REVISED

Create 6-7 individual social media graphics (square size) to encourage folks to join our online course called:

The Harvest Ledger Circle
How to Launch a Multi-Million Business From Scratch
Sign Up Today!

IMPORTANT: Make the largest and most prominent text on the graphic be: How to Launch a Multi-Million Business From Scratch

For the color scheme of the graphics, let's try a blue color palette; make sure the graphics appeal to both men and women

Make sure each graphic contains 1 of the 3 pics attached (crop pic as needed); and make sure one of the graphics is all TEXT only.

Target Market(s)

men and women looking to start a business

Industry/Entity Type

Entrepreneurship

Colors
0054AA
0677BA
7BADD7
CADEEF
E8F1F8

Requirements
Must have
• All the text and use the 3 pics provided; one graphic can be all text; Simple, modern design that's easy to read

```html
<!DOCTYPE html>
<html lang="en">
<head>
<meta charset="utf-8">
<title>The Harvest Ledger Circle – Sign Up</title>
<link rel="stylesheet" href="https://fonts.googleapis.com/css2?family=Russo+One&family=Archivo+Black&display=swap">
<style>
  :root {
    --blue-deep: #0054AA;
    --blue-mid: #0677BA;
    --blue-soft: #7BADD7;
    --blue-pale: #CADEEF;
    --blue-mist: #E8F1F8;
    --glow: #5cc4ee;
    --navy: #0d1836;
    --charcoal: #161d2b;
    --denim: #1d4f8f;
    --white: #ffffff;
    --silver-a: #e4e7ec;
    --silver-b: #8e949c;
  }
  * { margin: 0; padding: 0; box-sizing: border-box; }
  html, body { width: 1200px; height: 1200px; overflow: hidden; background: var(--blue-deep); }
  .poster {
    position: relative;
    width: 1200px; height: 1200px;
    background: radial-gradient(circle at 50% 45%, var(--glow) 0%, var(--blue-mid) 38%, var(--blue-deep) 78%);
    overflow: hidden;
  }
  .frame {
    position: absolute; inset: 16px;
    border: 9px solid var(--silver-b);
    border-image: linear-gradient(135deg, var(--silver-a), var(--silver-b), var(--silver-a), var(--silver-b)) 1;
  }
  .title-box {
    position: absolute; left: 214px; top: 55px; width: 772px; height: 106px;
    background: var(--navy);
    border: 6px solid var(--white);
    border-radius: 28px;
    display: flex; align-items: center; justify-content: center;
  }
  .title-top, .title-main {
    font-family: "Russo One", sans-serif;
    color: var(--white);
    text-transform: uppercase;
  }
  .title-top { font-size: 62px; line-height: 1; letter-spacing: 3px; }
  .title-main {
    position: absolute; left: 0; right: 0; top: 168px;
    text-align: center; font-size: 96px; line-height: 1; letter-spacing: 10px;
    text-shadow: 0 6px 0 rgba(13,24,54,0.45);
  }
  .photo {
    position: absolute; left: 205px; top: 262px; width: 776px; height: 566px;
    border-radius: 120px 120px 0 0;
    background:
      linear-gradient(90deg, var(--charcoal) 0%, var(--charcoal) 46%, var(--denim) 58%, var(--denim) 100%);
    -webkit-mask-image: linear-gradient(180deg, rgba(0,0,0,0.55) 0%, rgba(0,0,0,0.9) 45%, rgba(0,0,0,0.6) 85%, rgba(0,0,0,0) 100%);
    mask-image: linear-gradient(180deg, rgba(0,0,0,0.55) 0%, rgba(0,0,0,0.9) 45%, rgba(0,0,0,0.6) 85%, rgba(0,0,0,0) 100%);
  }
  .headline-panel {
    position: absolute; left: 84px; top: 832px; width: 1032px; height: 255px;
    background: var(--navy);
    border-radius: 46px;
    display: flex; align-items: center; justify-content: center;
    box-shadow: 0 0 18px rgba(92,196,238,0.35);
  }
  .headline {
    font-family: "Archivo Black", sans-serif;
    color: var(--blue-mist);
    text-transform: uppercase;
    text-align: center;
    font-size: 67px; line-height: 78px;
  }
  .cta {
    position: absolute; left: 0; right: 0; top: 1106px;
    text-align: center;
    font-family: "Archivo Black", sans-serif;
    color: var(--white);
    font-size: 46px; line-height: 1;
    text-transform: uppercase;
  }
</style>
</head>
<body>
  <main class="poster">
    <div class="frame"></div>

    <header>
      <div class="title-box"><span class="title-top">The Harvest Ledger</span></div>
      <div class="title-main">Circle</div>
    </header>

    <div class="photo" role="img" aria-label="Photo of the two course hosts standing side by side, smiling, one in a black turtleneck with arms crossed and one in a denim blazer, against a blue backdrop"></div>

    <section class="headline-panel">
      <h1 class="headline">How to Launch a<br>Multi-Million Business<br>From Scratch</h1>
    </section>

    <p class="cta">Sign Up Today!</p>
  </main>
</body>
</html>
```